Business card design for my company.
I would like the card's background colour to be black. You can also see our web site to get an idea of our brand. https://www.tmwhomecrafting.com.au/
- Name
- Email

```html
<!DOCTYPE html>
<html lang="en">
<head>
<meta charset="utf-8">
<title>TMW Home Crafting – Business Card</title>
<link rel="stylesheet" href="https://fonts.googleapis.com/css2?family=Roboto:wght@300;400;700;900&display=swap">
<style>
  :root {
    --stage: #2b2b2b;
    --card-black: #1c1c1e;
    --card-black-deep: #101012;
    --pattern-tone: #262628;
    --brand-green: #17984a;
    --ink-white: #ffffff;
  }
  * { margin: 0; padding: 0; box-sizing: border-box; }
  html, body {
    width: 1200px; height: 800px; overflow: hidden;
    background: var(--stage);
    font-family: "Roboto", sans-serif;
  }
  .stage {
    position: relative; width: 1200px; height: 800px;
    display: flex; flex-direction: column; align-items: center; justify-content: center; gap: 40px;
  }
  .card {
    position: relative; width: 595px; height: 340px;
    border-radius: 26px; overflow: hidden;
    box-shadow: 0 14px 30px rgba(0,0,0,.55);
  }

  /* Front */
  .card--front { background: var(--card-black); }
  .front-texture {
    position: absolute; inset: 0;
    background: linear-gradient(135deg, var(--pattern-tone), var(--card-black-deep));
  }
  .brand-lockup {
    position: absolute; display: flex; align-items: center; gap: 12px;
    color: var(--ink-white); font-weight: 900; letter-spacing: .12em; text-transform: uppercase;
    white-space: nowrap;
  }
  .brand-lockup__mark { background: var(--brand-green); flex: none; }
  .card--front .brand-lockup {
    left: 50%; top: 50%; transform: translate(-50%, -50%); font-size: 30px;
  }
  .card--front .brand-lockup__mark { width: 28px; height: 28px; }

  /* Back */
  .card--back { background: var(--brand-green); }
  .back-panel { position: absolute; inset: 0; width: 100%; height: 100%; }
  .card--back .brand-lockup { left: 250px; top: 44px; font-size: 22px; }
  .card--back .brand-lockup__mark { width: 20px; height: 20px; }

  .contact {
    position: absolute; left: 250px; top: 128px; color: var(--ink-white);
  }
  .contact__name { font-size: 34px; line-height: 1; white-space: nowrap; }
  .contact__first { font-weight: 900; }
  .contact__last { font-weight: 300; }
  .contact__role { font-size: 16px; font-weight: 400; margin-top: 4px; }
  .contact__list { list-style: none; margin-top: 20px; }
  .contact__item {
    display: flex; align-items: center; gap: 10px;
    font-size: 15.5px; font-weight: 400; line-height: 27px; white-space: nowrap;
  }
  .contact__icon { width: 16px; height: 16px; flex: none; }
</style>
</head>
<body>
<main class="stage">

  <section class="card card--front" aria-label="Card front">
    <div class="front-texture" role="img" aria-label="Embossed dark chevron texture across the card"></div>
    <div class="brand-lockup">
      <span class="brand-lockup__mark"></span>
      <span class="brand-lockup__name">TMW Home Crafting</span>
    </div>
  </section>

  <section class="card card--back" aria-label="Card back">
    <svg class="back-panel" viewBox="0 0 595 340" preserveAspectRatio="none" aria-hidden="true">
      <polygon points="0,0 70,0 210,150 205,340 0,340" fill="#1c1c1e"/>
      <polygon points="195,150 210,150 205,340 192,340" fill="#0c0c0d"/>
    </svg>

    <div class="brand-lockup">
      <span class="brand-lockup__mark"></span>
      <span class="brand-lockup__name">TMW Home Crafting</span>
    </div>

    <div class="contact">
      <p class="contact__name"><span class="contact__first">Liam</span> <span class="contact__last">Carver</span></p>
      <p class="contact__role">General Manager</p>
      <ul class="contact__list">
        <li class="contact__item">
          <svg class="contact__icon" viewBox="0 0 24 24" aria-hidden="true"><path fill="#fff" d="M6.6 10.8a15 15 0 0 0 6.6 6.6l2.2-2.2c.3-.3.7-.4 1-.2 1.1.4 2.3.6 3.6.6.6 0 1 .4 1 1V20c0 .6-.4 1-1 1A17 17 0 0 1 3 4c0-.6.4-1 1-1h3.5c.6 0 1 .4 1 1 0 1.3.2 2.5.6 3.6.1.3 0 .7-.2 1z"/></svg>
          0400 555 182
        </li>
        <li class="contact__item">
          <svg class="contact__icon" viewBox="0 0 24 24" aria-hidden="true"><circle cx="12" cy="12" r="9" fill="none" stroke="#fff" stroke-width="2"/><path d="M3 12h18M12 3c3 3 3 15 0 18M12 3c-3 3-3 15 0 18" fill="none" stroke="#fff" stroke-width="1.6"/></svg>
          www.tmwhomecrafting.com.au
        </li>
        <li class="contact__item">
          <svg class="contact__icon" viewBox="0 0 24 24" aria-hidden="true"><rect x="3" y="6" width="18" height="13" rx="1.5" fill="none" stroke="#fff" stroke-width="2"/><path d="M3 7l9 7 9-7" fill="none" stroke="#fff" stroke-width="2"/></svg>
          info@tmwhomecrafting.com.au
        </li>
        <li class="contact__item">
          <svg class="contact__icon" viewBox="0 0 24 24" aria-hidden="true"><path fill="#fff" d="M12 2a7 7 0 0 0-7 7c0 5 7 13 7 13s7-8 7-13a7 7 0 0 0-7-7zm0 9.5A2.5 2.5 0 1 1 12 6.5a2.5 2.5 0 0 1 0 5z"/></svg>
          Harrowvale, Northmere, Australia
        </li>
      </ul>
    </div>
  </section>

</main>
</body>
</html>
```